Veltrane Group Business Card Design

The CEO is looking for a new trendy look for his business card.
You can stay with current branding or come up with something new/creative. It can be 3D, including Medical Office buildings. You can use our logo in a variety of colors. Please include name, title, company name, company website, email address, cell number

Target Market(s)

Real Estate Development and Construction

Industry/Entity Type

Health care real estate

Contact Information for Business Card

Rohesh Kamdar, CEO M-604.781.2249 E-roheshkamdar@veltrane.com Address:4180 Lindqvist Ave, Tampa, FL 33482 www.veltrane.com

Font styles to use
Other font styles liked:
• Be creative

Requirements
Must have
• Creative, trendy look
Nice to have
• Please go to our website to get a feel- www. veltrane.com
Should not have
• small fonts

```html
<!DOCTYPE html>
<html lang="en">
<head>
<meta charset="utf-8">
<title>Veltrane Group Business Card</title>
<link rel="stylesheet" href="https://fonts.googleapis.com/css2?family=Roboto+Condensed:wght@300;400;700&display=swap">
<style>
  :root {
    --stage: #7399c6;
    --paper: #ffffff;
    --ink: #0a0a0a;
    --brand-red: #e60b24;
    --brand-red-dark: #a10617;
    --sketch-light: #eeeeee;
    --sketch-mid: #dcdcdc;
    --text-on-dark: #ffffff;
  }
  * { box-sizing: border-box; margin: 0; padding: 0; }
  html, body { width: 1200px; height: 912px; overflow: hidden; }
  body {
    background: var(--stage);
    font-family: "Roboto Condensed", "Arial Narrow", sans-serif;
    position: relative;
  }
  .card {
    position: absolute;
    left: 320px;
    width: 560px;
    height: 320px;
    background: var(--paper);
    overflow: hidden;
    box-shadow: 0 10px 28px rgba(0, 0, 0, 0.18);
  }
  .card--front { top: 116px; }
  .card--back  { top: 476px; }

  /* Front */
  .front-band { position: absolute; background: var(--ink); }
  .front-band--top { left: 0; top: 0; width: 100%; height: 22px; clip-path: polygon(0 0, 100% 0, 100% 100%, 3% 100%); }
  .front-band--bottom { left: 0; bottom: 0; width: 100%; height: 22px; clip-path: polygon(0 0, 97% 0, 100% 100%, 0 100%); }
  .front-sketch {
    position: absolute; left: 150px; top: 46px; width: 300px; height: 228px;
    background: linear-gradient(160deg, var(--sketch-light), #f8f8f8 70%);
  }
  .front-wordmark {
    position: absolute; left: 0; right: 0; top: 112px;
    text-align: center; color: var(--brand-red);
    font-weight: 700; font-size: 78px; line-height: 1; letter-spacing: -1px;
  }
  .plus-marks { position: absolute; }
  .plus-marks--front { left: 20px; bottom: 34px; }

  /* Back */
  .back-name-block {
    position: absolute; left: 0; top: 0; width: 330px; height: 92px;
    background: var(--ink); color: var(--text-on-dark);
    padding: 18px 0 0 22px; display: flex; align-items: center; gap: 14px;
  }
  .person-name { font-weight: 300; font-size: 30px; line-height: 1; letter-spacing: 0.5px; }
  .person-title { font-weight: 300; font-size: 18px; margin-top: 4px; }
  .back-contact-block {
    position: absolute; left: 0; top: 92px; width: 330px; height: 134px;
    background: var(--brand-red); color: var(--text-on-dark);
    border-top-right-radius: 14px;
    padding: 14px 0 0 22px;
    display: flex; flex-direction: column; gap: 9px;
  }
  .back-contact-fold {
    position: absolute; left: 330px; top: 206px; width: 14px; height: 20px;
    background: var(--brand-red-dark);
    clip-path: polygon(0 0, 100% 100%, 0 100%);
  }
  .back-web-block {
    position: absolute; left: 0; top: 226px; width: 380px; height: 94px;
    background: var(--ink); color: var(--text-on-dark);
    padding: 0 0 0 22px; display: flex; align-items: center; gap: 14px;
    clip-path: polygon(0 0, 100% 0, 100% 100%, 0 100%);
  }
  .contact-row { display: flex; align-items: center; gap: 14px; font-size: 17px; font-weight: 400; }
  .icon-disc { flex: none; width: 30px; height: 30px; }
  .back-wordmark {
    position: absolute; right: 22px; top: 18px;
    color: var(--brand-red); font-weight: 700; font-size: 44px; line-height: 1; letter-spacing: -1px;
  }
  .back-sketch {
    position: absolute; left: 392px; top: 80px; width: 150px; height: 226px;
    background: linear-gradient(180deg, #f4f4f4, var(--sketch-mid));
  }
  .plus-marks--back-top { left: 346px; top: 20px; }
  .plus-marks--back-bottom { left: 330px; top: 248px; }
</style>
</head>
<body>

  <section class="card card--front" aria-label="Business card front">
    <div class="front-band front-band--top"></div>
    <div class="front-sketch" role="img" aria-label="Faint line drawing of medical office buildings"></div>
    <div class="front-wordmark">Veltrane</div>
    <svg class="plus-marks plus-marks--front" width="60" height="36" viewBox="0 0 60 36" aria-hidden="true">
      <g stroke="#e60b24" stroke-width="3" stroke-linecap="square">
        <path d="M4 10h12M10 4v12"/>
        <path d="M36 8h12M42 2v12"/>
        <path d="M27 28h7M30.5 24.5v7"/>
      </g>
    </svg>
    <div class="front-band front-band--bottom"></div>
  </section>

  <section class="card card--back" aria-label="Business card back">
    <div class="back-name-block">
      <svg class="icon-disc" viewBox="0 0 30 30" aria-hidden="true">
        <circle cx="15" cy="15" r="15" fill="#e60b24"/>
        <circle cx="15" cy="15" r="10" fill="#fff"/>
        <circle cx="15" cy="12" r="3.2" fill="#e60b24"/>
        <path d="M9 21c1-4 11-4 12 0z" fill="#e60b24"/>
      </svg>
      <div>
        <div class="person-name">ROHESH KAMDAR</div>
        <div class="person-title">Manager</div>
      </div>
    </div>

    <div class="back-contact-block">
      <div class="contact-row">
        <svg class="icon-disc" viewBox="0 0 30 30" aria-hidden="true">
          <circle cx="15" cy="15" r="15" fill="#fff"/>
          <path d="M10 9l3 0 1.5 4-2 1.2a9 9 0 0 0 3.3 3.3l1.2-2 4 1.5 0 3c-6 1-12-5-11-11z" fill="#e60b24"/>
        </svg>
        <span>604.781.2249</span>
      </div>
      <div class="contact-row">
        <svg class="icon-disc" viewBox="0 0 30 30" aria-hidden="true">
          <circle cx="15" cy="15" r="15" fill="#fff"/>
          <path d="M15 7a5.5 5.5 0 0 0-5.5 5.5c0 4 5.5 10.5 5.5 10.5s5.5-6.5 5.5-10.5A5.5 5.5 0 0 0 15 7z" fill="#e60b24"/>
          <circle cx="15" cy="12.5" r="2" fill="#fff"/>
        </svg>
        <span>4180 Lindqvist Ave, Tampa, FL 33482</span>
      </div>
      <div class="contact-row">
        <svg class="icon-disc" viewBox="0 0 30 30" aria-hidden="true">
          <circle cx="15" cy="15" r="15" fill="#fff"/>
          <rect x="8" y="10" width="14" height="10" fill="#e60b24"/>
          <path d="M8 10l7 6 7-6" fill="none" stroke="#fff" stroke-width="1.4"/>
        </svg>
        <span>E-roheshkamdar@veltrane.com</span>
      </div>
    </div>
    <div class="back-contact-fold"></div>

    <div class="back-web-block">
      <svg class="icon-disc" viewBox="0 0 30 30" aria-hidden="true">
        <circle cx="15" cy="15" r="15" fill="#e60b24"/>
        <g fill="none" stroke="#fff" stroke-width="1.6">
          <circle cx="15" cy="15" r="7"/>
          <ellipse cx="15" cy="15" rx="3" ry="7"/>
          <path d="M8 15h14"/>
        </g>
      </svg>
      <span class="contact-row">www. veltrane.com</span>
    </div>

    <div class="back-wordmark">Veltrane</div>
    <svg class="plus-marks plus-marks--back-top" width="40" height="30" viewBox="0 0 40 30" aria-hidden="true">
      <g stroke="#e60b24" stroke-width="2.4">
        <path d="M2 8h9M6.5 3.5v9"/>
        <path d="M20 10h9M24.5 5.5v9"/>
        <path d="M14 22h5M16.5 19.5v5"/>
      </g>
    </svg>
    <svg class="plus-marks plus-marks--back-bottom" width="40" height="44" viewBox="0 0 40 44" aria-hidden="true">
      <g stroke="#fff" stroke-width="2.6">
        <path d="M4 10h6M7 7v6"/>
        <path d="M20 10h12M26 4v12"/>
        <path d="M24 32h12M30 26v12"/>
      </g>
    </svg>
    <div class="back-sketch" role="img" aria-label="Line drawing of a medical office tower"></div>
  </section>

</body>
</html>
```